NEW Modern Sleek Business Card for VR Language Startup

Our startup is using VR to lead the next wave of world language education. We need a two-sided business card that introduces the larger organization (Brightloom Language Inc) and our contact info on one side and shows the product, Glimwoorld, on the other side.

Side 1 (contact info)= Brightloom Logo and Contact info (name, title, phone, email)

Side 2 (product)= Glimworld logo, text, and website
Text= Culturally Immersive Language Learning Games
Website= www.glimworld-play.com

Target Market(s)

Education, Technology

Contact Information for Business Card

Contact info will be updated upon approval of the design. For now, put this as a placeholder.

Perry Dunmore
Founder & CEO
pdunmore@quillpost-mail.net
(555)-014-2286

Font styles to use
Other font styles liked:
• Gibson and Century Gothic are the brand fonts

Requirements
Nice to have
• I would love to see cohesion between the design and colors of the two logos. I have attached a few business card designs that I like, so you can get a feel for my preferred style.

```html
<!DOCTYPE html>
<html lang="en">
<head>
<meta charset="utf-8">
<title>Brightloom Language — Business Card</title>
<link rel="stylesheet" href="https://fonts.googleapis.com/css2?family=Montserrat:wght@600;700&family=Questrial&display=swap">
<style>
  :root{
    --stage:#3b3b3e;
    --card-dark:#0a0a0a;
    --card-mid:#1e1e1e;
    --card-light:#2a2a2a;
    --white:#ffffff;
    --muted:#d8d8d8;
    --blue:#4d8ff5;
    --violet:#6a5cf5;
    --orange:#f8703a;
    --red:#f2304f;
    --purple:#9152c4;
    --cyan:#1de3e8;
  }
  *{box-sizing:border-box;margin:0;padding:0}
  html,body{width:1200px;height:1200px;overflow:hidden}
  body{background:var(--stage);position:relative;font-family:"Questrial",sans-serif}
  .card{
    position:absolute;left:220px;width:760px;height:434px;border-radius:26px;overflow:hidden;
    background:linear-gradient(120deg,var(--card-dark) 0%,var(--card-mid) 60%,var(--card-light) 100%);
    box-shadow:0 18px 40px rgba(0,0,0,.45);
  }
  .card--product{top:100px}
  .card--contact{top:620px}

  /* product side */
  .product{display:flex;flex-direction:column;align-items:center;justify-content:center;height:100%;text-align:center}
  .brand-mark{display:flex;align-items:center;gap:16px}
  .brand-mark__dot{width:46px;height:46px;border-radius:50%}
  .product .brand-mark__dot{background:var(--blue)}
  .product__name{font-family:"Montserrat",sans-serif;font-weight:700;font-size:64px;color:var(--blue);letter-spacing:1px}
  .product__tagline{margin-top:18px;font-size:21px;color:var(--blue);letter-spacing:.5px}
  .product__url{margin-top:52px;font-family:"Montserrat",sans-serif;font-weight:700;font-size:19px;color:var(--violet);letter-spacing:.5px}

  /* contact side */
  .contact__logo{position:absolute;left:150px;top:92px}
  .contact .brand-mark__dot{background:var(--red)}
  .contact__company{font-family:"Montserrat",sans-serif;font-weight:700;font-size:44px;color:var(--white);letter-spacing:3px;text-transform:uppercase}
  .contact__details{position:absolute;left:150px;top:238px;display:flex;align-items:center;gap:22px}
  .person{text-align:right}
  .person__name{font-family:"Montserrat",sans-serif;font-weight:700;font-size:28px;color:var(--white);text-transform:uppercase}
  .person__title{font-size:17px;color:var(--muted);margin-top:4px}
  .divider{width:2px;height:62px;background:var(--red)}
  .lines{list-style:none;display:flex;flex-direction:column;gap:10px}
  .lines li{display:flex;align-items:center;gap:12px;font-size:17px;color:var(--white)}
  .lines svg{width:18px;height:18px;flex:none}
  .color-band{position:absolute;left:0;right:0;bottom:0;height:24px;display:flex;gap:3px;background:#000}
  .color-band span{flex:1}
  .color-band .orange{background:var(--orange)}
  .color-band .red{background:var(--red)}
  .color-band .purple{background:var(--purple)}
  .color-band .cyan{background:var(--cyan)}
</style>
</head>
<body>

<section class="card card--product" aria-label="Product side">
  <div class="product">
    <div class="brand-mark">
      <span class="brand-mark__dot"></span>
      <span class="product__name">Glimworld</span>
    </div>
    <p class="product__tagline">Culturally Immersive Language Learning Games</p>
    <p class="product__url">www.glimworld-play.com</p>
  </div>
</section>

<section class="card card--contact contact" aria-label="Contact side">
  <div class="contact__logo brand-mark">
    <span class="brand-mark__dot"></span>
    <span class="contact__company">Brightloom Language</span>
  </div>

  <div class="contact__details">
    <div class="person">
      <p class="person__name">Perry Dunmore</p>
      <p class="person__title">President</p>
    </div>
    <span class="divider"></span>
    <ul class="lines">
      <li>
        <svg viewBox="0 0 20 20" aria-hidden="true"><rect x="2" y="4" width="16" height="12" rx="1.5" fill="none" stroke="#f2304f" stroke-width="1.8"/><path d="M2.5 5 L10 11 L17.5 5" fill="none" stroke="#f2304f" stroke-width="1.8"/></svg>
        pdunmore@quillpost-mail.net
      </li>
      <li>
        <svg viewBox="0 0 20 20" aria-hidden="true"><path d="M5 2.5 L8 2.5 L9.5 6.5 L7.5 8 C8.5 10 10 11.5 12 12.5 L13.5 10.5 L17.5 12 L17.5 15 C17.5 16.5 16.5 17.5 15 17.5 C8.5 17 3 11.5 2.5 5 C2.5 3.5 3.5 2.5 5 2.5Z" fill="#f2304f"/></svg>
        (555)-014-2286
      </li>
    </ul>
  </div>

  <div class="color-band" aria-hidden="true">
    <span class="orange"></span><span class="red"></span><span class="purple"></span><span class="cyan"></span>
  </div>
</section>

</body>
</html>
```